Unique Business Card Design

Unique Business Card design for our orthotic and prosthetic company. Our logo is on our website, color is light blue. Unique shape (artificial leg shaped, vertical, etc..) preferred. Logo, business name, individual name and basic demographics needed.

Industry/Entity Type

Business

Contact Information for Business Card

Logo, Industry, Phone # Logo, "Prosthetic & Orthotic Services" Place to add individual name and contact info

Colors
cee9f5

Requirements
Must have
• The icon must be there, placement of "Prosthetic & Orthotic Services" can be moved
Nice to have
• Like the mix of light blue, and a little darker blue. One design included the icons from my website which was a nice touch

```html
<!DOCTYPE html>
<html lang="en">
<head>
<meta charset="utf-8">
<title>Limbwell Inc – Business Card</title>
<link rel="stylesheet" href="https://fonts.googleapis.com/css2?family=Open+Sans:wght@400;600&family=Cormorant+Garamond:ital,wght@1,500&display=swap">
<style>
  :root {
    --brand-blue: #0d72d2;
    --ink: #1d1d1f;
    --card-face: #f7f8fa;
    --backdrop: #e4e7eb;
    --band-text: #ffffff;
  }
  * { box-sizing: border-box; margin: 0; padding: 0; }
  html, body {
    width: 1200px; height: 900px; overflow: hidden;
    background: var(--backdrop);
    font-family: "Open Sans", Arial, sans-serif;
  }
  .card {
    position: absolute; left: 100px; top: 142px;
    width: 1000px; height: 615px;
    background: var(--card-face);
    border-radius: 28px; overflow: hidden;
    box-shadow: 0 12px 40px rgba(0,0,0,0.12);
  }
  .brand-mark {
    position: absolute; left: 153px; top: 95px;
    width: 180px; height: 180px; border-radius: 50%;
    background: var(--brand-blue);
  }
  .brand-name {
    position: absolute; left: 380px; top: 112px;
    font-size: 58px; font-weight: 600; letter-spacing: 1px;
    color: var(--brand-blue); line-height: 1;
  }
  .brand-tagline {
    position: absolute; left: 420px; top: 200px;
    font-family: "Cormorant Garamond", Georgia, serif;
    font-style: italic; font-weight: 500;
    font-size: 32px; color: var(--brand-blue);
  }
  .person {
    position: absolute; right: 526px; top: 355px; text-align: right;
  }
  .person-name {
    font-size: 34px; font-weight: 600; color: var(--brand-blue); line-height: 1.1;
  }
  .person-title {
    font-size: 26px; color: var(--ink); margin-top: 4px;
  }
  .divider {
    position: absolute; left: 500px; top: 357px;
    width: 2px; height: 86px; background: var(--brand-blue);
  }
  .contact-list {
    position: absolute; left: 528px; top: 342px; list-style: none;
  }
  .contact-list li {
    display: flex; align-items: center; gap: 10px;
    font-size: 27px; color: var(--ink); height: 36px;
  }
  .contact-list svg { width: 18px; height: 18px; fill: var(--brand-blue); flex: none; }
  .address-band {
    position: absolute; left: 0; bottom: 0; width: 100%; height: 116px;
    background: var(--brand-blue); color: var(--band-text);
    display: flex; align-items: center; justify-content: center;
    font-size: 27px;
  }
</style>
</head>
<body>
  <div class="card">
    <div class="brand-mark"></div>
    <div class="brand-name">LIMBWELL INC</div>
    <div class="brand-tagline">Prosthetic &amp; Orthotic Services</div>

    <div class="person">
      <div class="person-name">DANIEL BROOKS</div>
      <div class="person-title">Managing Director</div>
    </div>
    <div class="divider"></div>

    <ul class="contact-list">
      <li>
        <svg viewBox="0 0 24 24" aria-hidden="true"><path d="M6.6 10.8a15 15 0 0 0 6.6 6.6l2.2-2.2a1 1 0 0 1 1-.25 11.4 11.4 0 0 0 3.6.57 1 1 0 0 1 1 1V20a1 1 0 0 1-1 1A17 17 0 0 1 3 4a1 1 0 0 1 1-1h3.5a1 1 0 0 1 1 1c0 1.25.2 2.45.57 3.57a1 1 0 0 1-.25 1z"/></svg>
        <span>(555) 014-2290</span>
      </li>
      <li>
        <svg viewBox="0 0 24 24" aria-hidden="true"><path d="M2 5h20v14H2z M2 5l10 8 10-8" stroke="#fff" stroke-width="1.5"/></svg>
        <span>info@limbwellinc.com</span>
      </li>
      <li>
        <svg viewBox="0 0 24 24" aria-hidden="true"><circle cx="12" cy="12" r="10"/><path d="M2 12h20M12 2c3 3 3 17 0 20M12 2c-3 3-3 17 0 20" fill="none" stroke="#fff" stroke-width="1.3"/></svg>
        <span>www.limbwellinc.com</span>
      </li>
    </ul>

    <div class="address-band">1234, Address Goes Here Country Name, 123456</div>
  </div>
</body>
</html>
```